Create modern and sleek business card for luxury real estate company

We're a "boutique" real estate office looking for a design that gets across a highly modern luxury brand. Blacks and whites are probably the best colors unless we try a silver foil for the logo. I've attached a version of our current logo here. I'd like to swap out the current font on there with Gotham Light Regular.

I'm looking to have one side of the card have the logo with the space for our agents info on the other side.

Target Market(s)

Young professionals in a "luxury" headspace

Industry/Entity Type

Real estate

Contact Information for Business Card

A place for agent name, cell number, website. The slogan "Simply Rethinking Real Estate".

Font styles to use
Other font styles liked:
• Gotham Regular

Colors

Designer to choose only greyscale colors for use in the design.

Requirements
Must have
• Matte black as the background color. Clean lines and use of contrast. A specific design aspect that will use silver foil.
Nice to have
• Up in the air on integrating a QR code
Should not have
• Any houses or other real estate related design (ex: a clip art house)

```html
<!DOCTYPE html>
<html lang="en">
<head>
<meta charset="utf-8">
<title>Halden Realty – Business Card</title>
<link rel="stylesheet" href="https://fonts.googleapis.com/css2?family=Montserrat:wght@300;400;600&display=swap">
<style>
  :root {
    --stage: #161616;
    --card: #2f2f2f;
    --card-edge: #262626;
    --deboss: #1c1c1c;
    --foil: #f2f2f2;
    --text-soft: #d9d9d9;
    --rule: #5a5a5a;
  }
  html, body {
    margin: 0;
    width: 1200px;
    height: 900px;
    overflow: hidden;
    background: var(--stage);
    font-family: "Montserrat", sans-serif;
  }
  .canvas {
    position: relative;
    width: 1200px;
    height: 900px;
  }
  .card {
    position: absolute;
    width: 620px;
    height: 354px;
    background: var(--card);
    box-shadow: 0 18px 40px rgba(0,0,0,0.55);
    border: 1px solid var(--card-edge);
    box-sizing: border-box;
  }
  .card--front { left: 170px; top: 60px; }
  .card--back  { left: 410px; top: 486px; }

  .brand {
    position: absolute;
    display: flex;
    align-items: center;
    gap: 14px;
  }
  .brand__circle {
    flex: none;
    border-radius: 50%;
    border: 2px solid currentColor;
    box-sizing: border-box;
  }
  .brand__name {
    font-weight: 400;
    text-transform: uppercase;
    line-height: 1.05;
    letter-spacing: 0.08em;
  }

  .card--front .brand {
    left: 50%; top: 50%;
    transform: translate(-50%, -50%);
    color: var(--deboss);
  }
  .card--front .brand__circle { width: 84px; height: 84px; }
  .card--front .brand__name { font-size: 38px; }

  .card--back .brand {
    left: 40px; top: 50%;
    transform: translateY(-50%);
    color: var(--foil);
  }
  .card--back .brand__circle { width: 54px; height: 54px; }
  .card--back .brand__name { font-size: 24px; }

  .divider {
    position: absolute;
    left: 300px; top: 24px;
    width: 1px; height: 306px;
    background: linear-gradient(to bottom, transparent, var(--rule) 30%, var(--rule) 70%, transparent);
  }

  .agent {
    position: absolute;
    left: 330px; top: 66px;
    color: var(--foil);
  }
  .agent__name {
    margin: 0;
    font-size: 22px;
    font-weight: 600;
    letter-spacing: 0.02em;
  }
  .agent__title {
    margin: 2px 0 18px;
    font-size: 14px;
    font-weight: 300;
    color: var(--text-soft);
  }
  .contact {
    list-style: none;
    margin: 0 0 16px;
    padding: 0 0 0 18px;
    font-size: 14.5px;
    font-weight: 400;
  }
  .contact__item {
    display: flex;
    align-items: center;
    gap: 8px;
    margin-bottom: 5px;
  }
  .contact__icon { width: 14px; height: 14px; flex: none; }
  .address {
    margin: 0;
    padding-left: 40px;
    font-style: normal;
    font-size: 14.5px;
    line-height: 1.35;
  }
</style>
</head>
<body>
<main class="canvas">

  <section class="card card--front" aria-label="Card front">
    <div class="brand">
      <span class="brand__circle"></span>
      <span class="brand__name">Halden<br>Realty</span>
    </div>
  </section>

  <section class="card card--back" aria-label="Card back">
    <div class="brand">
      <span class="brand__circle"></span>
      <span class="brand__name">Halden<br>Realty</span>
    </div>

    <div class="divider"></div>

    <div class="agent">
      <h1 class="agent__name">MARCUS ELLERY</h1>
      <p class="agent__title">Managing Director</p>
      <ul class="contact">
        <li class="contact__item">
          <svg class="contact__icon" viewBox="0 0 16 16" fill="none" stroke="#f2f2f2" stroke-width="1.6" stroke-linecap="round" stroke-linejoin="round"><path d="M3 2h3l1.5 3.5-2 1.2a8 8 0 0 0 3.8 3.8l1.2-2L14 10v3a1 1 0 0 1-1 1A11 11 0 0 1 2 3a1 1 0 0 1 1-1z"/></svg>
          044-987 654 321
        </li>
        <li class="contact__item">
          <svg class="contact__icon" viewBox="0 0 16 16" fill="none" stroke="#f2f2f2" stroke-width="1.6" stroke-linejoin="round"><rect x="1.5" y="3.5" width="13" height="9"/><path d="M1.5 3.5 8 9l6.5-5.5"/></svg>
          hello@haldenrealty.com
        </li>
        <li class="contact__item">
          <svg class="contact__icon" viewBox="0 0 16 16" fill="none" stroke="#f2f2f2" stroke-width="1.3"><circle cx="8" cy="8" r="6.3"/><ellipse cx="8" cy="8" rx="2.8" ry="6.3"/><path d="M1.7 8h12.6M2.8 4.8h10.4M2.8 11.2h10.4"/></svg>
          www.haldenrealty.com
        </li>
      </ul>
      <address class="address">18, Linden Court Avenue<br>20417, Northvale</address>
    </div>
  </section>

</main>
</body>
</html>
```